Revamp Kestrelo Inc website

A complete revamp of the www.kestrelo-app.com website.
Strong actionable landing pages.
An in-house site was being done but was abandoned. See http://www.sitebuildly.com/dmorvane/kestrelo and once in, click on the "Home" to go to the main Home page.
Updates

A new YouTube Standard Video has just been posted: http://www.clipvista.com/watch?v=Q-T8ma4zLpW&feature=email

I thought that I would share what was being done in-house, but was abandoned.

Once launched you will come to the main landing page, then click on the "Home" button to see the main home page. I thought this was rather interesting. One problem here is Flash, most smartphones don't support Flash and our market is in that world, so Flash really is not a good option.

Reason: Please can you submit one more design, we have a dead tie with voting.

Reason: Request as per a designer.

Target Market(s)

Kestrelo for all intense purposes is mobile RoadHalo on steroids. Currently running on Android, BB and iPhone. End of Jan 2012 we will run on ANY J2ME (Java) supported phone as well. Here we will be talking directly to the OBD (onboard diagnostics) in the car. In the event of the car's airbags being deployed emergency services, ES, (whether public, 911 or other country equivalent, or private, alarm company) the application will not only call the ES but also log the gps information. Other services include: SOS, Nurse Lines, Roadside, Notify Friends and Family.
Kestrelo determines the ERC by the phones location, thus assuming not private in the USA will reach out to 911, Europe 112 etc.

Kestrelo is about making a pro and re active emergency solution to the masses. It must be affordable to anyone owning a cell phone (thus: 9 cents per day). The emphasis is on the person not the asset as RoadHalo and other competitors are. It must be adaptable to ones environment

Kestrelo target market sale is a top-down (Corporate to consumer) we do offer:
* white-labeling (see www.guardlinemobileus.com) as well as non branded solutions (Kestrelo branded),
* private emergency response center call and data routing - here the emergency call is routed the the companies emergency call center (example: alarm company, security firm, campus police), and the location and user details data details on file are pushed as well.

As such our target corporate market primarily is:
Security, Home Alarm, Insurance, University Campus Police, Auto, Smartphone users, Roadside assistance

Our ultimate target audience is cell phone users, where security, safety and peace of mind of oneself, family and/or team members is of importance.

Requirements
Must have
• Must have strong actionable call to action features
Must have multiple actionable landing pages
Must link to our ecommerce
Must link into blog
Must be able to cellphone friendly (i.e.: no flash)
Must be SEO

```html
<!DOCTYPE html>
<html lang="en">
<head>
<meta charset="utf-8">
<title>Kestrelo, Inc — Home</title>
<link rel="stylesheet" href="https://fonts.googleapis.com/css2?family=Source+Sans+3:wght@400;600;700&family=Noto+Sans:wght@400&display=swap">
<style>
:root{
  --navy:#1b3550;
  --nav-blue:#1d5f9d;
  --nav-active:#3f86c6;
  --sky:#4fb3e6;
  --feature-blue:#2d8bc4;
  --feature-dark:#1f6fa6;
  --text:#2b2b2b;
  --muted:#555;
  --border:#c9ccd0;
  --footer:#1c5f94;
  --white:#fff;
}
*{box-sizing:border-box;margin:0;padding:0}
html,body{width:810px;height:1200px;overflow:hidden;background:var(--white)}
body{position:relative;font-family:"Source Sans 3",sans-serif;color:var(--text)}
.abs{position:absolute}
a{color:inherit}
h1,h2,h3,h4{font-weight:400}

/* header */
.header{left:0;top:0;width:810px;height:66px;background:linear-gradient(#fff,#eef0f2)}
.brand{left:40px;top:21px;font-size:24px;font-weight:600;letter-spacing:3px;color:var(--navy)}
.connect{left:549px;top:40px;font-size:10px;letter-spacing:.5px;color:#444}
.social{top:38px;width:14px;height:14px;background:#3a74b5}
.signup{left:709px;top:30px;width:67px;height:21px;border-radius:3px;background:linear-gradient(#5cb6ea,#2a86c8);color:#fff;font-size:11px;font-weight:700;text-align:center;line-height:21px;text-decoration:none}

/* nav */
.nav{left:0;top:66px;width:810px;height:37px;background:var(--nav-blue);display:flex;padding-left:54px}
.nav a{font-size:12px;color:#fff;text-decoration:none;line-height:37px;padding:0 16px;border-right:1px solid #4a80b6;height:37px}
.nav a:last-of-type{border-right:none}
.nav a.active{background:var(--nav-active);padding:0 10px}
.search{left:615px;top:77px;width:137px;height:15px;border-radius:8px;background:#fff;font-size:9px;color:#333;padding-left:7px;line-height:15px}

/* hero */
.hero{left:0;top:103px;width:810px;height:232px;background:radial-gradient(circle at 35% 45%,#8fd3f5 0%,var(--sky) 55%,#3a9fd6 100%)}
.hero-devices{left:100px;top:110px;width:362px;height:216px;border-radius:6px;background:linear-gradient(90deg,#4a5560,#1f2830 50%,#3b4652)}
.hero-title{left:472px;top:145px;width:300px;font-size:20px;font-weight:700;color:var(--navy);line-height:26px}
.hero-text{left:474px;top:202px;width:248px;font-size:9.4px;line-height:12.4px;color:#fff}
.view-more{left:483px;top:275px;width:63px;height:17px;border-radius:3px;background:#fff;font-size:10px;color:#2c6da3;text-align:center;line-height:17px;text-decoration:underline}

/* service tabs */
.band{left:0;top:335px;width:810px;height:72px;background:linear-gradient(#dadcde,#eceef0 70%,#fff)}
.tabs{left:57px;top:350px;width:698px;height:47px;display:flex;border:1px solid var(--border);background:linear-gradient(#fff,#e5e7e9)}
.tab{flex:1;display:flex;align-items:center;gap:8px;padding-left:14px;font-size:15px;color:#6a6e72;border-right:1px solid var(--border)}
.tab:last-child{border-right:none}
.tab.active{background:#fff}

/* main */
.h-section{font-size:16px;color:#111}
.welcome{left:51px;top:439px}
.intro{left:51px;top:463px;width:470px;font-family:"Noto Sans",sans-serif;font-size:9.6px;line-height:11.3px;color:var(--muted)}
.intro u{color:#222}
.read-more{left:51px;top:606px;font-family:"Noto Sans",sans-serif;font-size:10px;color:#222;text-decoration:none}
.rule{left:49px;top:631px;width:479px;border-top:1px dashed #b5b8bb}
.videos-title{left:48px;top:647px}
.video{left:48px;top:677px;width:335px;height:201px;border:3px solid #111;background:#d6d6d6}

.product{top:905px;width:223px;height:221px;border:1px solid var(--border);border-radius:8px;background:linear-gradient(#fff 70%,#f6f6f7)}
.product-head{height:48px;border-bottom:1px solid var(--border);padding:7px 0 0 13px;position:relative}
.product-name{font-size:15px;color:#111}
.product-desc{font-size:9px;color:#333;margin-top:1px}
.product-icon{position:absolute;right:10px;top:4px;width:38px;height:38px;border-radius:50%;background:radial-gradient(circle at 40% 35%,#3f74c0,#16305f)}
.product-body{padding:20px 16px 0 15px;font-size:9px;line-height:11px;color:#222}
.product-body p+p{margin-top:3px}
.product-link{position:absolute;right:12px;bottom:14px;font-size:9px;font-weight:700;color:#111;text-decoration:underline}

/* sidebar */
.sidebar{left:547px;top:418px;width:223px;height:690px;background:linear-gradient(90deg,#e9eaec,#fafafa 30%)}
.features{left:563px;top:432px;width:208px;height:273px;border-radius:4px;background:linear-gradient(var(--feature-blue),var(--feature-dark))}
.features h3{font-size:16px;color:#e8f4fb;height:33px;line-height:33px;padding-left:16px;background:linear-gradient(#44a3d8,#2f8fc8);border-radius:4px 4px 0 0;border-bottom:1px solid #6bb8e2}
.features ul{list-style:none;padding:9px 0 0 18px}
.features li{font-size:10px;color:#fff;line-height:17.9px}
.news-title{left:570px;top:732px;font-size:15px;color:#111}
.news{left:570px;width:188px}
.news h4{font-size:12px;color:#111}
.news p{font-size:8.5px;line-height:10.8px;color:#222;margin-top:2px}
.news .date{display:block;font-size:9px;text-decoration:underline;margin-top:4px;color:#222}

/* footer */
.footer{left:0;top:1153px;width:810px;height:47px;background:var(--footer);color:#fff;font-size:10px}
.copyright{left:51px;top:11px}
.footer-links{right:31px;top:12px;display:flex}
.footer-links a{text-decoration:none;padding:0 7.5px;border-left:1px solid #7fa7cc}
.footer-links a:first-child{border-left:none}
.footer-links a:last-child{padding-right:0}
</style>
</head>
<body>

<header class="header abs">
  <div class="brand abs">KESTRELO, INC</div>
  <div class="connect abs">CONNECT WITH</div>
  <span class="social abs" style="left:632px" aria-label="Social network"></span>
  <span class="social abs" style="left:648px" aria-label="Social network"></span>
  <span class="social abs" style="left:664px;background:#4aa8d8" aria-label="Social network"></span>
  <span class="social abs" style="left:680px;background:#c94a3c" aria-label="Video channel"></span>
  <a class="signup abs" href="#">SIGN UP</a>
</header>

<nav class="nav abs">
  <a class="active" href="#">HOME</a>
  <a href="#">ABOUT</a>
  <a href="#">SERVICES</a>
  <a href="#">PARTNERS</a>
  <a href="#">CONTACT</a>
  <a href="#">PURCHASE</a>
  <a href="#">LOGIN</a>
</nav>
<div class="search abs">search here
  <svg class="abs" style="right:6px;top:3px" width="9" height="9" viewBox="0 0 9 9"><circle cx="3.5" cy="3.5" r="2.6" fill="none" stroke="#222" stroke-width="1.3"/><line x1="5.5" y1="5.5" x2="8.5" y2="8.5" stroke="#222" stroke-width="1.5"/></svg>
</div>

<section class="hero abs"></section>
<div class="hero-devices abs" role="img" aria-label="Tablet and smartphones showing the mobile application home screens"></div>
<h1 class="hero-title abs">Your Mobile Application Lines goes here</h1>
<p class="hero-text abs">The only way to success is through the right path and that’s what we provide you. None of the other companies has the result we do. So stick to the best that’s how you will be the best don’t opt for the second best. Our expertise does not limit itself to web development</p>
<a class="view-more abs" href="#">view more</a>

<div class="band abs"></div>
<div class="tabs abs">
  <div class="tab active">
    <svg width="26" height="26" viewBox="0 0 26 26"><circle cx="13" cy="13" r="12" fill="#2a2d31"/><circle cx="13" cy="13" r="9" fill="#5d646b"/><path d="M13 6v7l5 3" stroke="#fff" stroke-width="1.6" fill="none"/></svg>
    Your Services 1st</div>
  <div class="tab">
    <svg width="28" height="26" viewBox="0 0 28 26"><rect x="3" y="4" width="8" height="18" rx="3" fill="#2a2d31"/><rect x="17" y="4" width="8" height="18" rx="3" fill="#2a2d31"/><rect x="10" y="9" width="8" height="5" fill="#2a2d31"/></svg>
    Your Services IInd</div>
  <div class="tab">
    <svg width="28" height="28" viewBox="0 0 28 28" stroke="#1d3550" stroke-width="2" fill="none"><circle cx="14" cy="14" r="8"/><circle cx="14" cy="14" r="2.5"/><path d="M14 2v24M2 14h24M5.5 5.5l17 17M22.5 5.5l-17 17"/></svg>
    Your Services IIIrd</div>
  <div class="tab">
    <svg width="26" height="26" viewBox="0 0 26 26"><rect x="2" y="4" width="22" height="19" fill="#1d3c78"/><rect x="6" y="8" width="14" height="11" fill="#4f8fd8"/><circle cx="22" cy="4" r="3" fill="#2a7ad0"/></svg>
    Your Services IVth</div>
</div>

<main>
  <h2 class="h-section welcome abs">Welcome to our website home page</h2>
  <div class="intro abs">
    <p><u>Quorvantix eSolutions is a web service company, offering a wide range of services which range from designing and development, that is covering almost all the fields </u> in the best possible way. To be the best we know what and how to present beautifully the working of the client’s need and their advantages be highlighted. We act in accordance with the Industry certified processes to deliver the best to our clients all over the world. Over years we have built a strong reputation in providing website design and web development services.</p>
    <p style="margin-top:17px">Thus, Wanna get ahead in the competition with other websites…. Quorvantix esolutions provide you with an attractive and most convincing website to enhance your marketing goals.</p>
    <p style="margin-top:2px">The only way to success is through the right path and that’s what we provide you. None of the other companies has the result we do.</p>
  </div>
  <a class="read-more abs" href="#">read more about us</a>
  <div class="rule abs"></div>

  <h2 class="h-section videos-title abs">Watch Our Latest Vedios</h2>
  <div class="video abs" aria-label="Latest video player">
    <svg class="abs" style="left:150px;top:76px" width="36" height="40" viewBox="0 0 36 40"><path d="M0 0L36 20L0 40Z" fill="#fff"/></svg>
  </div>

  <article class="product abs" style="left:48px">
    <div class="product-head">
      <div class="product-name">Product Name</div>
      <div class="product-desc">Description of your application</div>
      <span class="product-icon"></span>
    </div>
    <div class="product-body">
      <p>Quorvantix eSolutions is a professional website design company dedicated to provide excellent services.We at Quorvantix eSolutions think graphic design as a combination and collabora-tion of ideas and technology.</p>
      <p>Our Website Design team give an unforgettable impression on the customers and the clients.We can assure you that this is the best place for requirement of yours regarding website design solutions</p>
    </div>
    <a class="product-link" href="#">read more about application</a>
  </article>
  <article class="product abs" style="left:292px;top:903px">
    <div class="product-head">
      <div class="product-name">Product Name</div>
      <div class="product-desc">Description of your application</div>
      <span class="product-icon"></span>
    </div>
    <div class="product-body">
      <p>Quorvantix eSolutions is a professional website design company dedicated to provide excellent services.We at Quorvantix eSolutions think graphic design as a combination and collabora-tion of ideas and technology.</p>
      <p>Our Website Design team give an unforgettable impression on the customers and the clients.We can assure you that this is the best place for requirement of yours regarding website design solutions</p>
    </div>
    <a class="product-link" href="#">read more about application</a>
  </article>
</main>

<aside>
  <div class="sidebar abs"></div>
  <section class="features abs">
    <h3>Our Features</h3>
    <ul>
      <li>Accident and Impact Management</li>
      <li>High Crime Area Alerts</li>
      <li>International and National SOS</li>
      <li>Cyber Alert Notification Management</li>
      <li>Personal Location Notification</li>
      <li>Homeland and Travel Status Notification</li>
      <li>&nbsp;24/7 Certified Nurse Line</li>
      <li>Traffic Alerts</li>
      <li>Auto Assistance</li>
      <li>Extensive Online Tracking</li>
      <li>Management Portal</li>
      <li>Weather Alert</li>
    </ul>
  </section>
  <h3 class="news-title abs">Latest News &amp; Updates</h3>
  <div class="news abs" style="top:760px">
    <h4>heading goes here</h4>
    <p>Quorvantix eSolutions is a professional website design company dedicated to provide excellent services.We at Quorvantix eSolutions think graphic design as a combination and collabora-tion of ideas and technology.</p>
    <a class="date" href="#">update 25 .11 2011</a>
  </div>
  <div class="news abs" style="top:867px">
    <h4>heading goes here</h4>
    <p>Quorvantix eSolutions is a professional website design company dedicated to provide excellent services.We at Quorvantix eSolutions think graphic design as a combination and collabora-tion of ideas and technology.</p>
    <a class="date" href="#">update 25 .11 2011</a>
  </div>
  <div class="news abs" style="top:974px">
    <h4>heading goes here</h4>
    <p>Quorvantix eSolutions is a professional website design company dedicated to provide excellent services.We at Quorvantix eSolutions think graphic design as a combination and collabora-tion of ideas and technology.</p>
    <a class="date" href="#">update 25 .11 2011</a>
  </div>
</aside>

<footer class="footer abs">
  <div class="copyright abs">copyrigth © 2011 company name&nbsp; All right reserved</div>
  <nav class="footer-links abs">
    <a href="#">home</a><a href="#">about us</a><a href="#">services</a><a href="#">partners</a><a href="#">features</a><a href="#">contact us</a>
  </nav>
</footer>

</body>
</html>
```